Website for a Steadwell, an HVAC company.

We are a company that provides residential and commercial service. We don’t need any widgets other than a call to action where customers can message us. Though we have very few google reviews, they are all great and would like to see those populated. Simple and modern is the style. I included our logo and a pic of our vans.

Target Market(s)

Residential customers

Coding

Coded - Design and coding required

Number of Pages Required

1 page

Font styles to use
Sans Serif

Colors
0054AA
0677BA
7BADD7
CADEEF
E8F1F8
EE7325
F08F49
F5BC92
FAE3D3
FDF4ED

```html
<!DOCTYPE html>
<html lang="en">
<head>
<meta charset="utf-8">
<title>Steadwell Heating and Air</title>
<link rel="stylesheet" href="https://fonts.googleapis.com/css2?family=Montserrat:wght@300;400;600;700;800&family=Roboto:wght@400;500;700&display=swap">
<style>
:root{
  --blue-deep:#0054AA;
  --blue:#0677BA;
  --blue-mid:#7BADD7;
  --blue-pale:#CADEEF;
  --blue-mist:#E8F1F8;
  --orange:#EE7325;
  --orange-soft:#F08F49;
  --orange-pale:#F5BC92;
  --orange-mist:#FAE3D3;
  --cream:#FDF4ED;
  --royal:#2f5de8;
  --rust:#c9451a;
  --ink:#1b1b1f;
  --text:#555a63;
  --navy:#141a2b;
  --white:#ffffff;
}
*{box-sizing:border-box;margin:0;padding:0}
html,body{width:1200px;height:4812px;overflow:hidden}
body{position:relative;background:var(--white);font-family:'Roboto',sans-serif;color:var(--text)}
.abs{position:absolute}
.h-font{font-family:'Montserrat',sans-serif}

/* top bar + header */
.topbar{left:580px;top:0;width:620px;height:52px;background:linear-gradient(90deg,var(--blue-deep),var(--royal));border-bottom-left-radius:26px;color:var(--white);font-size:15px;display:flex;align-items:center}
.topbar .item{display:flex;align-items:center;gap:14px;position:absolute}
.topbar .ico{width:30px;height:30px;border-radius:50%;background:var(--white);display:flex;align-items:center;justify-content:center}
.brand{left:112px;top:40px;width:150px;height:100px;display:flex;flex-direction:column;align-items:center;justify-content:center;gap:8px}
.brand .dot{width:44px;height:44px;border-radius:50%;background:var(--orange)}
.brand .name{font-family:'Montserrat',sans-serif;font-weight:800;font-size:17px;letter-spacing:2px;color:var(--blue-deep)}
.nav{top:80px;font-family:'Montserrat',sans-serif;font-weight:600;font-size:14px;color:var(--ink)}
.nav.active{color:var(--orange)}
.btn{display:flex;align-items:center;justify-content:center;gap:8px;font-family:'Montserrat',sans-serif;font-weight:700;font-size:13px;color:var(--white);letter-spacing:.5px;clip-path:polygon(4% 0,100% 0,96% 100%,0 100%)}
.btn.orange{background:linear-gradient(90deg,var(--rust),var(--orange))}
.btn.blue{background:linear-gradient(90deg,var(--royal),var(--blue))}
.btn .arr{width:13px;height:13px;border-radius:50%;background:var(--white);display:inline-block;position:relative}
.btn .arr::after{content:"";position:absolute;left:4px;top:3.5px;border-left:5px solid var(--orange);border-top:3px solid transparent;border-bottom:3px solid transparent}
.btn.blue .arr::after{border-left-color:var(--blue)}

/* hero */
.hero-left{left:0;top:127px;width:600px;height:578px;background:linear-gradient(160deg,#3f8be8,#1556c9 60%,#0c3c99)}
.hero-right{left:600px;top:127px;width:600px;height:578px;background:linear-gradient(180deg,#e8712b,#f09a52 45%,#b5531e)}
.hero-title1{left:359px;top:288px;width:486px;height:60px;background:var(--white);color:var(--ink);font-family:'Montserrat',sans-serif;font-weight:400;font-size:54px;line-height:60px;text-align:center}
.hero-title2{left:0;width:1200px;top:350px;text-align:center;color:var(--white);font-family:'Montserrat',sans-serif;font-weight:800;font-size:54px;letter-spacing:1px}
.slide-arrow{width:42px;height:42px;border-radius:50%;background:var(--white);top:355px;display:flex;align-items:center;justify-content:center}
.chat{left:994px;top:505px;width:172px;height:50px;background:var(--white);border-radius:25px;display:flex;align-items:center;font-size:13px;color:var(--ink);box-shadow:0 4px 10px rgba(0,0,0,.15)}
.chat .bubble{width:60px;height:60px;border-radius:50%;background:var(--royal);margin-left:-4px;margin-right:10px;display:flex;align-items:center;justify-content:center}
.scroll{left:562px;top:658px;width:76px;height:76px;border-radius:50%;background:var(--white);box-shadow:0 4px 14px rgba(0,0,0,.15);display:flex;align-items:center;justify-content:center}

/* section headings */
.sec-title{font-family:'Montserrat',sans-serif;font-size:34px;color:var(--ink);line-height:1.2}
.sec-title b{font-weight:800}
.sec-title span{font-weight:400}
.underline{width:84px;height:4px;background:linear-gradient(90deg,var(--rust),var(--orange-soft));border-radius:2px}
.body-text{font-size:13px;line-height:24px;color:var(--text)}

/* about */
.about-bg{left:0;top:705px;width:1200px;height:572px;background:radial-gradient(circle at 80% 40%,var(--blue-mist),var(--white) 60%)}
.photo{border-radius:6px}
.badge{left:426px;top:922px;width:140px;height:138px;background:linear-gradient(160deg,var(--orange-soft),var(--rust));border-radius:6px;color:var(--white);text-align:center;font-family:'Montserrat',sans-serif;box-shadow:0 6px 16px rgba(0,0,0,.2)}
.badge .num{font-size:60px;font-weight:700;line-height:70px;margin-top:20px}
.badge .lbl{font-size:20px;font-weight:600}

/* services */
.services{left:0;top:1277px;width:1200px;height:705px;background:linear-gradient(120deg,#2a8fd4,#2f62e6 70%,#3356e9)}
.svc-card{top:1449px;width:469px;height:436px;background:var(--white);box-shadow:0 8px 20px rgba(0,0,0,.2)}
.svc-card .img{position:absolute;left:10px;top:10px;width:449px;height:252px}
.svc-card .ic{position:absolute;top:218px;right:40px;width:84px;height:84px;border-radius:50%;border:5px solid var(--white);display:flex;align-items:center;justify-content:center}
.svc-card h3{position:absolute;left:24px;top:288px;font-family:'Montserrat',sans-serif;font-weight:700;font-size:17px;color:var(--ink)}
.svc-card p{position:absolute;left:24px;top:322px;width:420px;font-size:13px;line-height:24px;color:var(--text)}
.svc-card .more{position:absolute;left:24px;top:388px;font-family:'Montserrat',sans-serif;font-weight:700;font-size:13px;display:flex;align-items:center;gap:8px}

/* why */
.why-text{width:220px;font-size:13px;line-height:24px;color:var(--text)}
.why-text h4{font-family:'Montserrat',sans-serif;font-weight:700;font-size:14px;color:var(--ink);margin-bottom:6px}
.why-left{text-align:right;left:122px}
.why-right{left:856px}

/* testimonials */
.testi{left:0;top:2519px;width:1200px;height:449px;background:linear-gradient(100deg,#c3401a,#e06a28 55%,#ee8d3c)}
.t-card{top:2678px;width:305px;height:198px;background:#f1f1f1;border-bottom:4px solid var(--blue-mid);box-shadow:0 6px 14px rgba(0,0,0,.2)}
.t-card .gcirc{position:absolute;left:26px;top:-18px;width:60px;height:60px;border-radius:50%;background:var(--white);box-shadow:0 3px 8px rgba(0,0,0,.15);display:flex;align-items:center;justify-content:center}
.t-card .gcirc i{width:24px;height:24px;border-radius:50%;border:4px solid var(--blue)}
.t-card .name{position:absolute;left:112px;top:14px;font-family:'Montserrat',sans-serif;font-weight:700;font-size:14px;color:var(--ink)}
.t-card .stars{position:absolute;left:112px;top:34px;color:var(--orange);font-size:14px;letter-spacing:2px}
.t-card p{position:absolute;left:32px;top:70px;width:250px;font-size:11.5px;line-height:20px;color:var(--text)}

/* footer */
.footer{left:0;top:4492px;width:1200px;height:320px;background:var(--navy);color:#e6e8ee;font-size:13px;line-height:22px}
.footer h5{font-family:'Montserrat',sans-serif;font-weight:600;font-size:13px;color:var(--white);margin-bottom:22px}
</style>
</head>
<body>

<!-- Top bar -->
<div class="abs topbar">
  <div class="item" style="left:40px">
    <span class="ico"><svg width="16" height="12" viewBox="0 0 16 12"><rect x="0.5" y="0.5" width="15" height="11" rx="1.5" fill="var(--blue-deep)"/><path d="M1 1l7 5 7-5" stroke="#fff" fill="none" stroke-width="1.3"/></svg></span>
    office@steadwellair.com
  </div>
  <div class="item" style="left:326px">
    <span class="ico"><svg width="14" height="14" viewBox="0 0 24 24"><path d="M6.6 10.8a15.1 15.1 0 006.6 6.6l2.2-2.2a1 1 0 011-.25 11.4 11.4 0 003.6.6 1 1 0 011 1V20a1 1 0 01-1 1A17 17 0 013 4a1 1 0 011-1h3.5a1 1 0 011 1c0 1.25.2 2.45.6 3.6a1 1 0 01-.25 1z" fill="var(--blue-deep)"/></svg></span>
    (555) 014-2290
  </div>
</div>

<!-- Header -->
<div class="abs brand">
  <span class="dot"></span>
  <span class="name">STEADWELL</span>
</div>
<div class="abs nav active" style="left:546px">HOME</div>
<div class="abs nav" style="left:613px">ABOUT US</div>
<div class="abs nav" style="left:708px">SERVICES ▾</div>
<div class="abs nav" style="left:810px">REVIEWS</div>
<div class="abs btn orange" style="left:922px;top:67px;width:159px;height:45px">CONTACT US</div>

<!-- Hero -->
<div class="abs hero-left" role="img" aria-label="Technician in a hard hat servicing an outdoor air conditioning unit, blue toned"></div>
<div class="abs hero-right" role="img" aria-label="Rooftop commercial HVAC units at sunset, orange toned"></div>
<div class="abs hero-title1">EXPERIENCE THE</div>
<div class="abs hero-title2">DIFFERENCE</div>
<div class="abs btn orange" style="left:482px;top:492px;width:238px;height:45px">GET A FREE ESTIMATE <span class="arr"></span></div>
<div class="abs slide-arrow" style="left:50px"><svg width="10" height="12"><path d="M8 1L2 6l6 5" stroke="#333" stroke-width="2" fill="none"/></svg></div>
<div class="abs slide-arrow" style="left:1106px"><svg width="10" height="12"><path d="M2 1l6 5-6 5" stroke="#333" stroke-width="2" fill="none"/></svg></div>
<div class="abs chat">
  <span class="bubble"><svg width="30" height="26" viewBox="0 0 30 26"><rect x="1" y="1" width="28" height="19" rx="4" fill="#fff"/><path d="M6 20v5l6-5z" fill="#fff"/><path d="M6 8h18M6 13h12" stroke="var(--royal)" stroke-width="2"/></svg></span>
  Chat With Us
</div>
<svg class="abs" style="left:262px;top:704px" width="60" height="42"><path d="M0 0h60L30 42z" fill="#1556c9"/></svg>
<svg class="abs" style="left:866px;top:704px" width="60" height="42"><path d="M0 0h60L30 42z" fill="#b5531e"/></svg>
<div class="abs scroll"><svg width="20" height="32"><rect x="1" y="1" width="18" height="30" rx="9" stroke="#888" fill="none" stroke-width="1.5"/><rect x="9" y="7" width="2" height="7" rx="1" fill="#888"/></svg></div>

<!-- About -->
<div class="abs about-bg"></div>
<div class="abs photo" style="left:112px;top:789px;width:404px;height:406px;background:linear-gradient(160deg,#6f8a5c,#a7a79b 55%,#8a8f92)" role="img" aria-label="Portrait of the company owner outdoors"></div>
<div class="abs badge"><div class="num">20</div><div class="lbl">YEARS</div></div>
<div class="abs sec-title" style="left:682px;top:824px"><b>ABOUT</b> <span>US</span></div>
<div class="abs underline" style="left:682px;top:870px"></div>
<p class="abs body-text" style="left:682px;top:894px;width:404px">Welcome to Steadwell Heating and Air, your trusted partner in reliable and affordable heating and cooling solutions since 2003. Proudly serving Bayport and the surrounding areas, we bring over 20 years of expertise to every project. Our commitment to excellence has earned us the trust of the community, establishing Steadwell Heating and Air as a beacon of quality HVAC services. From our inception,</p>
<div class="abs btn blue" style="left:682px;top:1101px;width:163px;height:43px">LEARN MORE <span class="arr"></span></div>
<div class="abs" style="left:882px;top:1110px;width:34px;height:34px;border-radius:50%;background:linear-gradient(160deg,var(--orange-soft),var(--rust));display:flex;align-items:center;justify-content:center"><svg width="14" height="14" viewBox="0 0 24 24"><path d="M6.6 10.8a15.1 15.1 0 006.6 6.6l2.2-2.2a1 1 0 011-.25 11.4 11.4 0 003.6.6 1 1 0 011 1V20a1 1 0 01-1 1A17 17 0 013 4a1 1 0 011-1h3.5a1 1 0 011 1c0 1.25.2 2.45.6 3.6a1 1 0 01-.25 1z" fill="#fff"/></svg></div>
<div class="abs" style="left:929px;top:1098px;font-size:13px;color:var(--text)">Contact us today at</div>
<div class="abs h-font" style="left:929px;top:1118px;font-size:22px;font-weight:600;color:var(--ink)">(555) 014-2290</div>

<!-- Services -->
<div class="abs services"></div>
<div class="abs sec-title" style="left:0;width:1200px;text-align:center;top:1348px;color:var(--white)"><b>OUR</b> <span>SERVICES</span></div>
<div class="abs underline" style="left:558px;top:1394px;background:linear-gradient(90deg,var(--white),var(--orange-soft))"></div>

<div class="abs svc-card" style="left:107px">
  <div class="img" role="img" aria-label="Hands in a knit sweater warming over a home radiator" style="background:linear-gradient(120deg,#d9d9d9,#9a9a9a 45%,#e7e7e7)"></div>
  <div class="ic" style="background:linear-gradient(160deg,var(--orange-soft),var(--rust))"><svg width="36" height="34" viewBox="0 0 36 34"><path d="M3 16L18 3l15 13M7 13v18h22V13" stroke="#fff" stroke-width="2.4" fill="none"/><rect x="14" y="20" width="8" height="11" stroke="#fff" stroke-width="2" fill="none"/></svg></div>
  <h3>RESIDENTIAL SERVICE</h3>
  <p>Our skilled technicians diagnose and address specific issues affecting the system.</p>
  <div class="more" style="color:var(--rust)">LEARN MORE <svg width="13" height="13"><circle cx="6.5" cy="6.5" r="6.5" fill="var(--rust)"/><path d="M5 3.5l3.5 3-3.5 3" stroke="#fff" fill="none" stroke-width="1.5"/></svg></div>
</div>
<div class="abs svc-card" style="left:613px">
  <div class="img" role="img" aria-label="Rows of commercial rooftop HVAC units under a sunset sky" style="background:linear-gradient(180deg,#e8a05a,#7a7f8c 50%,#5c6370)"></div>
  <div class="ic" style="background:linear-gradient(160deg,#4b8ff0,var(--royal))"><svg width="34" height="34" viewBox="0 0 34 34"><rect x="4" y="6" width="14" height="24" stroke="#fff" stroke-width="2.2" fill="none"/><rect x="18" y="13" width="12" height="17" stroke="#fff" stroke-width="2.2" fill="none"/><path d="M8 11h6M8 16h6M8 21h6M22 18h4M22 23h4" stroke="#fff" stroke-width="2"/></svg></div>
  <h3>COMMERCIAL SERVICE</h3>
  <p>We inspect various components, &nbsp;fine-tune system settings, and check for potential issues.</p>
  <div class="more" style="color:var(--blue-deep)">LEARN MORE <svg width="13" height="13"><circle cx="6.5" cy="6.5" r="6.5" fill="var(--blue-deep)"/><path d="M5 3.5l3.5 3-3.5 3" stroke="#fff" fill="none" stroke-width="1.5"/></svg></div>
</div>

<!-- Why choose -->
<div class="abs" style="left:0;top:1982px;width:1200px;height:537px;background:radial-gradient(circle at 50% 20%,var(--blue-mist),var(--white) 55%)"></div>
<div class="abs sec-title" style="left:0;width:1200px;text-align:center;top:2060px"><b>WHY</b> <span>CHOOSE</span></div>
<div class="abs underline" style="left:558px;top:2106px"></div>
<svg class="abs" style="left:0;top:1982px" width="1200" height="537" viewBox="0 0 1200 537">
  <g stroke="var(--blue)" stroke-width="1.6" fill="none">
    <path d="M436 204h30l71 25"/><path d="M436 369h30l71-40"/>
    <path d="M764 204h-30l-71 25"/><path d="M764 369h-30l-71-40"/>
  </g>
  <circle cx="600" cy="292" r="122" fill="none" stroke="var(--orange-pale)" stroke-width="2"/>
  <circle cx="600" cy="292" r="108" fill="#fff" stroke="var(--orange)" stroke-width="2"/>
  <circle cx="600" cy="292" r="92" fill="var(--orange)"/>
  <circle cx="600" cy="292" r="64" fill="none" stroke="#fff" stroke-width="3"/>
  <g stroke="#fff" stroke-width="3.5" fill="none" stroke-linejoin="round">
    <path d="M574 294l26-22 26 22"/>
    <path d="M581 288v26h38v-26"/>
    <path d="M594 314v-13h12v13"/>
  </g>
  <g fill="var(--blue)"><circle cx="436" cy="204" r="5"/><circle cx="436" cy="369" r="5"/><circle cx="764" cy="204" r="5"/><circle cx="764" cy="369" r="5"/></g>
  <g fill="var(--rust)" stroke="#fff" stroke-width="2"><circle cx="537" cy="229" r="7"/><circle cx="537" cy="329" r="7"/><circle cx="663" cy="229" r="7"/><circle cx="663" cy="329" r="7"/></g>
  <g>
    <circle cx="389" cy="204" r="36" fill="var(--royal)" stroke="var(--blue-pale)" stroke-width="4"/>
    <circle cx="389" cy="369" r="36" fill="var(--royal)" stroke="var(--blue-pale)" stroke-width="4"/>
    <circle cx="811" cy="204" r="36" fill="var(--royal)" stroke="var(--blue-pale)" stroke-width="4"/>
    <circle cx="811" cy="369" r="36" fill="var(--royal)" stroke="var(--blue-pale)" stroke-width="4"/>
  </g>
  <g stroke="#fff" stroke-width="2" fill="none">
    <circle cx="389" cy="204" r="15"/><path d="M382 204l5 5 9-10"/>
    <circle cx="389" cy="369" r="15"/><path d="M389 361v8l5 4"/>
    <path d="M811 189l13 5v9c0 8-6 13-13 16-7-3-13-8-13-16v-9z"/><path d="M805 204l4 4 8-8"/>
    <circle cx="811" cy="369" r="15"/><path d="M811 361v16M815 364h-6a3 3 0 000 5h4a3 3 0 010 5h-6"/>
  </g>
</svg>
<div class="abs why-text why-left" style="top:2147px"><h4>CUSTOMER SATISFACTION</h4>Your satisfaction is our priority. We work diligently to exceed your expectations and provide personalized solutions.</div>
<div class="abs why-text why-left" style="top:2313px"><h4>COMMUNITY FOCUS</h4>We're proud to serve Bayport and its surrounding islands. It is our way giving back to the community</div>
<div class="abs why-text why-right" style="top:2147px"><h4>QUALITY SERVICE</h4>Our experienced technicians are committed to delivering quality service and ensuring your HVAC system operates at its best.</div>
<div class="abs why-text why-right" style="top:2313px"><h4>AFFORDABILITY</h4>We offer competitive pricing and transparent quotes to get your needed services without breaking the bank.</div>

<!-- Testimonials -->
<div class="abs testi"></div>
<div class="abs sec-title" style="left:0;width:1200px;text-align:center;top:2584px;color:var(--white)"><b>OUR</b> <span>TESTIMONIALS</span></div>
<div class="abs underline" style="left:558px;top:2630px;background:linear-gradient(90deg,var(--white),var(--orange-pale))"></div>

<div class="abs t-card" style="left:112px">
  <div class="gcirc"><i></i></div>
  <div class="name">RENEE T</div><div class="stars">★★★★★</div>
  <p>This was my first time using Steadwell Heating and Air and I was extremely impressed with the prompt service and fair pricing. As a property manager, I work with a lot of contractors and those are two...</p>
</div>
<div class="abs t-card" style="left:447px">
  <div class="gcirc"><i></i></div>
  <div class="name">DANA K</div><div class="stars">★★★★★</div>
  <p>I was surprised that Steadwell Heating and Air actually reached out to me after six months for my no charge follow up visit. I couldn't be happier with this company. On time service as well as professional...</p>
</div>
<div class="abs t-card" style="left:782px">
  <div class="gcirc"><i></i></div>
  <div class="name">GLORIA P</div><div class="stars">★★★★★</div>
  <p>Very thorough inspection. Highly recommend.</p>
</div>

<!-- Commitment -->
<div class="abs" style="left:0;top:2968px;width:1200px;height:1068px;background:radial-gradient(circle at 15% 30%,var(--blue-mist),var(--white) 45%)"></div>
<div class="abs photo" style="left:112px;top:3056px;width:404px;height:404px;background:linear-gradient(170deg,#6d8a52,#8f9590 50%,#5f6366)" role="img" aria-label="Company service truck parked in a lot"></div>
<div class="abs photo" style="left:415px;top:3173px;width:165px;height:163px;border:3px solid #fff;background:linear-gradient(150deg,#c9a27e,#e8e2da 55%,#a7642f);box-shadow:0 6px 14px rgba(0,0,0,.25)" role="img" aria-label="Technician servicing an indoor air handler"></div>
<div class="abs sec-title" style="left:682px;top:3096px"><b>OUR COMMITMENT TO</b><br><span>EXCELLENCE</span></div>
<p class="abs body-text" style="left:682px;top:3200px;width:412px">When you choose Steadwell Heating and Air, you select a team that cares about your comfort and peace of mind. We're here to keep your home cozy and your air system running smoothly. Ready to experience steadwell HVAC services? Contact us today to schedule an appointment or request a free consultation.</p>
<div class="abs btn blue" style="left:684px;top:3344px;width:163px;height:45px">BOOK NOW <span class="arr"></span></div>

<!-- Clean air -->
<div class="abs sec-title" style="left:112px;top:3573px"><b>CLEAN AIR QUALITY</b> <span>EQUALS</span><br><span>A HAPPY HOME</span></div>
<p class="abs body-text" style="left:112px;top:3680px;width:412px">If your house smells stuffy due to your pets or excessive moisture, consider upgrading the air filters or installing air purifiers. We are happy to consult you on air products that could improve your and your family's quality of life. Additionally, remember to ask us how you can save hundreds on your energy bills with energy-saving tips that only the pros know about!</p>
<div class="abs btn blue" style="left:116px;top:3854px;width:159px;height:45px">BOOK NOW <span class="arr"></span></div>
<div class="abs photo" style="left:677px;top:3536px;width:404px;height:404px;background:linear-gradient(180deg,#6a7a62,#2e3136 50%,#8d8f91)" role="img" aria-label="Rear of the company service truck with branded tailgate"></div>
<div class="abs photo" style="left:595px;top:3652px;width:164px;height:165px;border:3px solid #fff;background:linear-gradient(150deg,#b98a5c,#e4ddd2 55%,#8d5a2e);box-shadow:0 6px 14px rgba(0,0,0,.25)" role="img" aria-label="Technician replacing an air filter"></div>

<!-- Map -->
<div class="abs" style="left:0;top:4036px;width:1200px;height:456px;background:linear-gradient(160deg,#e9ecef 0%,#dfe8de 30%,#9fd0e8 55%,#8ec6e4 100%)" role="img" aria-label="Map of the service area along the coast and barrier islands"></div>

<!-- Footer -->
<div class="abs footer">
  <div class="abs" style="left:112px;top:50px;width:150px;display:flex;flex-direction:column;align-items:center;gap:10px">
    <span style="width:44px;height:44px;border-radius:50%;background:var(--orange)"></span>
    <span class="h-font" style="font-weight:800;font-size:17px;letter-spacing:2px;color:var(--blue-mid)">STEADWELL</span>
  </div>
  <div class="abs" style="left:295px;top:64px">(555) 014-2290<br>office@steadwellair.com</div>
  <div class="abs" style="left:295px;top:131px">Mon - Fri &nbsp;&nbsp;7:30am - 5:30pm<br>Saturday &nbsp;&nbsp;9:00am - 2:00pm<br>Sunday &nbsp;&nbsp;By Request Only</div>
  <div class="abs" style="left:587px;top:64px"><h5>Our Services</h5>Heating<br>Cooling<br>Energy Saving<br>Products</div>
  <div class="abs" style="left:783px;top:64px"><h5>Areas We Serve</h5>Bayport<br>Cedar Point<br>Gull Beach<br>Maple Hollow<br>Heron Isle</div>
  <div class="abs" style="left:982px;top:108px">North Bayport<br>Sandpiper Island<br>Willow Creek<br>Marsh Island<br>Oyster Island</div>
  <div class="abs" style="left:168px;top:239px;width:864px;height:1px;background:#39405a"></div>
  <div class="abs" style="left:0;top:262px;width:1200px;text-align:center;font-size:12px">Copyright@2025.All Rights Reserved</div>
</div>

</body>
</html>
```